BrivoTerna. Lantern of the Steady Harvest. Business card

Professional business card for BrivoTerna (Lantern of the Steady Harvest)
My rationale: Strategy-> Execution-> Results-> Value that lead to the BrivoTerna name: We put the Lantern of the Steady Harvest.
We deliver value to our customers helping them at defining a good strategy (cyan arrow). 90% of well formulated strategies fail due to poor execution so we also consider strategical execution very important (green arrow). Due to the execution we obtain the results (blue arrow). Finally, the results provide feedback to redefine strategy, and the new strategy has to be executed and new results obtained providing new feedback and on and on. It's like a wheel that finally, must create corporate value: value for shareholders, staholders, employees, providers...-

Target Market(s)

CEOs and steering comitees , invewrnent funds

Industry/Entity Type

Business Consultant

Contact Information for Business Card

Teodoro Vinsquel
CEO & Founder
teodoro.vinsquel@brivoterna-example.com
Mobile: +34 655.803.912
www.brivoterna-example.com

Colors

Designer to choose colors to be used in the design.

Requirements
Nice to have
• Nice to hace the words: Strategy, execution, results
• Nice to vave the claim: Lantern of the Steady Harvest
• The three colors should be shown:
• cyan for STRATEGY
• green for EXECUTION
• blue for RESULTS
Should not have
• Complete black background

```html
<!DOCTYPE html>
<html lang="en">
<head>
<meta charset="utf-8">
<title>BrivoTerna – Business Card</title>
<link href="https://fonts.googleapis.com/css2?family=Arimo:wght@400;700&family=Open+Sans:wght@400;600&display=swap" rel="stylesheet">
<style>
  :root {
    --backdrop: #2b2b2d;
    --card-white: #ffffff;
    --card-dark: #111a2e;
    --card-dark-edge: #0b1222;
    --brand-blue: #0a3a9c;
    --brand-cyan: #2fb6ea;
    --brand-green: #8cc63f;
    --text-dark: #2a2a2a;
    --divider: #c9cbd3;
    --back-text: #f2f2f2;
    --back-muted: #b9c2d6;
  }
  * { margin: 0; padding: 0; box-sizing: border-box; }
  html, body {
    width: 1200px; height: 960px; overflow: hidden;
    background: var(--backdrop);
  }
  .canvas { position: relative; width: 1200px; height: 960px; }
  .card {
    position: absolute; left: 250px; width: 700px; height: 400px;
    border-radius: 4px; overflow: hidden;
    box-shadow: 0 12px 30px rgba(0,0,0,.45);
  }

  /* Back side */
  .card-back {
    top: 50px;
    background: radial-gradient(ellipse at 50% 40%, var(--card-dark) 0%, var(--card-dark-edge) 100%);
  }
  .back-mark {
    position: absolute; left: 0; right: 0; top: 108px;
    display: flex; align-items: center; justify-content: center; gap: 14px;
  }
  .back-mark .mark-square { width: 28px; height: 28px; background: var(--brand-cyan); }
  .back-mark .mark-name {
    font-family: "Arimo", Arial, sans-serif; font-weight: 700;
    font-size: 52px; color: var(--back-text); letter-spacing: -1px;
  }
  .back-tagline {
    position: absolute; left: 0; right: 0; top: 180px; text-align: center;
    font-family: "Open Sans", Arial, sans-serif; font-size: 16px;
    letter-spacing: 1.5px; color: var(--back-muted);
  }
  .value-steps {
    position: absolute; left: 170px; right: 170px; top: 222px;
    display: flex; gap: 8px; list-style: none;
  }
  .value-steps li {
    flex: 1; padding-top: 10px; text-align: center;
    font-family: "Open Sans", Arial, sans-serif; font-size: 12px; font-weight: 600;
    letter-spacing: 2px; text-transform: uppercase; color: var(--back-text);
    border-top: 5px solid;
  }
  .value-steps .step-strategy { border-color: var(--brand-cyan); }
  .value-steps .step-execution { border-color: var(--brand-green); }
  .value-steps .step-results { border-color: var(--brand-blue); }
  .back-web {
    position: absolute; left: 0; right: 0; top: 300px; text-align: center;
    font-family: "Open Sans", Arial, sans-serif; font-size: 19px;
    letter-spacing: 3px; color: var(--back-text);
  }

  /* Front side */
  .card-front { top: 500px; background: var(--card-white); }
  .front-brand {
    position: absolute; left: 42px; top: 140px;
    display: flex; align-items: center; gap: 12px;
  }
  .front-brand .mark-square { width: 22px; height: 22px; background: var(--brand-blue); }
  .front-brand .mark-name {
    font-family: "Arimo", Arial, sans-serif; font-weight: 700;
    font-size: 40px; color: var(--brand-blue); letter-spacing: -1px;
  }
  .front-divider {
    position: absolute; left: 318px; top: 95px; width: 1px; height: 150px;
    background: var(--divider);
  }
  .contact {
    position: absolute; left: 340px; top: 102px;
    font-family: "Open Sans", Arial, sans-serif; color: var(--text-dark);
  }
  .contact-name {
    font-family: "Arimo", Arial, sans-serif; font-weight: 700;
    font-size: 26px; color: var(--brand-blue); line-height: 1.1;
  }
  .contact-role {
    font-family: "Arimo", Arial, sans-serif; font-size: 16px;
    color: var(--text-dark); margin-bottom: 14px;
  }
  .contact-list { list-style: none; }
  .contact-list li {
    display: flex; align-items: center; gap: 9px;
    font-size: 15px; line-height: 25px;
  }
  .contact-list svg { width: 14px; height: 14px; flex: none; }
  .front-rule {
    position: absolute; left: 0; right: 0; bottom: 66px; height: 2px;
    background: var(--brand-cyan);
  }
  .front-band {
    position: absolute; left: 0; right: 0; bottom: 0; height: 58px;
    background: var(--brand-blue);
    display: flex; align-items: center; padding-left: 130px;
    font-family: "Open Sans", Arial, sans-serif; font-size: 17px;
    color: var(--card-white); letter-spacing: .3px;
  }
</style>
</head>
<body>
<main class="canvas">

  <section class="card card-back" aria-label="Business card, back">
    <div class="back-mark">
      <span class="mark-square"></span>
      <span class="mark-name">BrivoTerna</span>
    </div>
    <p class="back-tagline">Lantern of the Steady Harvest</p>
    <ul class="value-steps">
      <li class="step-strategy">Strategy</li>
      <li class="step-execution">Execution</li>
      <li class="step-results">Results</li>
    </ul>
    <p class="back-web">www.brivoterna-example.com</p>
  </section>

  <section class="card card-front" aria-label="Business card, front">
    <div class="front-brand">
      <span class="mark-square"></span>
      <span class="mark-name">BrivoTerna</span>
    </div>
    <div class="front-divider"></div>
    <div class="contact">
      <p class="contact-name">Teodoro Vinsquel</p>
      <p class="contact-role">CEO &amp; Founder</p>
      <ul class="contact-list">
        <li>
          <svg viewBox="0 0 14 14" aria-hidden="true"><rect x="2" y="1.5" width="10" height="11" rx="1.5" fill="none" stroke="#2fb6ea" stroke-width="1.5"/></svg>
          +34 655.803.912
        </li>
        <li>
          <svg viewBox="0 0 14 14" aria-hidden="true"><rect x="1" y="3" width="12" height="8" fill="#2fb6ea"/><path d="M1 3 L7 8 L13 3" fill="none" stroke="#fff" stroke-width="1.2"/></svg>
          teodoro.vinsquel@brivoterna-example.com
        </li>
        <li>
          <svg viewBox="0 0 14 14" aria-hidden="true"><circle cx="7" cy="7" r="5.8" fill="none" stroke="#2fb6ea" stroke-width="1.3"/><ellipse cx="7" cy="7" rx="2.6" ry="5.8" fill="none" stroke="#2fb6ea" stroke-width="1"/><line x1="1.2" y1="7" x2="12.8" y2="7" stroke="#2fb6ea" stroke-width="1"/></svg>
          www.brivoterna-example.com
        </li>
      </ul>
    </div>
    <div class="front-rule"></div>
    <div class="front-band">Avda. Lumen 418, Barcelona , 08099, Spain</div>
  </section>

</main>
</body>
</html>
```